Business Card For Halvenmoor Financial Consulting

Hi, I would like a business card designed. Bold, modern.
Please use the same design as the logo. I have also attached the website design to see the overall theme.
Wordmark Font
Color: Hex: #01AEF7

```html
<!DOCTYPE html>
<html lang="en">
<head>
<meta charset="utf-8">
<title>Halvenmoor Financial Consulting – Business Card</title>
<link href="https://fonts.googleapis.com/css2?family=Montserrat:wght@700&family=Open+Sans:wght@400;600&display=swap" rel="stylesheet">
<style>
  :root {
    --navy: #0b3d63;
    --navy-deep: #0a3559;
    --sky: #3aa8e0;
    --white: #ffffff;
    --stage: #e9ecef;
  }
  * { margin: 0; padding: 0; box-sizing: border-box; }
  html, body { width: 1200px; height: 801px; overflow: hidden; }
  body {
    background: var(--stage);
    position: relative;
    font-family: "Open Sans", Arial, sans-serif;
  }
  .card {
    position: absolute;
    top: 246px;
    width: 540px;
    height: 309px;
    overflow: hidden;
    box-shadow: 0 6px 18px rgba(0,0,0,0.18);
  }
  .card--front { left: 40px; background: var(--navy); color: var(--white); }
  .card--back { left: 620px; background: var(--white); }

  .brand { position: absolute; display: flex; align-items: center; }
  .brand__square { border: 4px solid var(--sky); }
  .brand__name {
    font-family: "Montserrat", Arial, sans-serif;
    font-weight: 700;
    letter-spacing: 0.02em;
    line-height: 1;
  }
  .card--front .brand { left: 30px; top: 40px; gap: 12px; }
  .card--front .brand__square { width: 34px; height: 34px; }
  .card--front .brand__name { font-size: 24px; color: var(--white); }

  .card--back .brand { left: 50px; top: 120px; gap: 22px; }
  .card--back .brand__square { width: 66px; height: 66px; border-width: 6px; }
  .card--back .brand__name { font-size: 48px; color: var(--navy); }

  .contact { position: absolute; left: 30px; top: 112px; }
  .contact__name {
    font-family: "Montserrat", Arial, sans-serif;
    font-weight: 700;
    font-size: 19px;
    letter-spacing: 0.02em;
  }
  .contact__role { font-size: 13px; margin-bottom: 12px; }
  .contact__address { font-size: 12.5px; line-height: 1.4; margin-bottom: 12px; }
  .contact__list { list-style: none; font-size: 12.5px; line-height: 1.55; }
  .contact__list li { display: flex; align-items: center; gap: 8px; }
  .contact__list svg { width: 11px; height: 11px; fill: var(--sky); flex: none; }

  .feature-frame {
    position: absolute;
    left: 300px;
    top: 40px;
    width: 210px;
    height: 210px;
    border: 16px solid var(--sky);
    background: var(--navy-deep);
  }
</style>
</head>
<body>
  <section class="card card--front" aria-label="Business card front">
    <div class="brand">
      <span class="brand__square"></span>
      <span class="brand__name">HALVENMOOR</span>
    </div>

    <div class="contact">
      <p class="contact__name">COLIN MARSH</p>
      <p class="contact__role">Managing Director</p>
      <p class="contact__address">Your address, City<br>State, Zip 1234</p>
      <ul class="contact__list">
        <li>
          <svg viewBox="0 0 12 12" aria-hidden="true"><path d="M2.5 1l2 2.2-1 1.3c.7 1.5 1.8 2.6 3.3 3.3l1.3-1L10.3 9 9 11C4.8 10.5 1.5 7.2 1 3z"/></svg>
          123 456 789
        </li>
        <li>
          <svg viewBox="0 0 12 12" aria-hidden="true"><path d="M1 2.5h10v7H1z M1.6 3l4.4 3.5L10.4 3" stroke="#0b3d63" stroke-width=".9"/></svg>
          info@yourgmail.com
        </li>
        <li>
          <svg viewBox="0 0 12 12" aria-hidden="true"><circle cx="6" cy="6" r="5"/><path d="M1 6h10M6 1c-2 2.8-2 7.2 0 10M6 1c2 2.8 2 7.2 0 10" stroke="#0b3d63" stroke-width=".8" fill="none"/></svg>
          www.yourwebsite.com
        </li>
      </ul>
    </div>

    <div class="feature-frame" aria-hidden="true"></div>
  </section>

  <section class="card card--back" aria-label="Business card back">
    <div class="brand">
      <span class="brand__square"></span>
      <span class="brand__name">HALVENMOOR</span>
    </div>
  </section>
</body>
</html>
```